Small Business Directory Site Requires a Professional Responsive Web Design

Small Business Directory and Coupon Site - we require a complete website design for a brand new responsive & mobile friendly website. We already have a coder who will professional code our website in Magento.

All PSD pages need to be professionally designed then uploaded into a sharedrive (i.e. like filecrate). Additionally, as I cannot pre-empt everything, please note that we may require a little more assistance once the files have been transferred (for example, in www.brightlane-listings.example if you hover your mouse on the search box you will see a pop up box. We want one of these too and I think that means there may be extra design work here)

We have some draft page sketches have been created (there are some minor changes we want to the sketches provided though); however, we require an excellent designer to add the creative touches to it to make it look professionally created. All artwork/font must be legal.

-------------------------
We like the look of the www.brightlane-listings.example and www. marlowfolio.example

For the headers, please consider a font similar to RNS camellia. We likes this style, but it is too thin for the headers...so we need a variation like this one. For the copy/general text font, something basic that marries well with the headers.

---------------------

Please be sure to also read the brief we wrote for the coder as this will help with better understanding our design requirements.

In total I believe we have about 50 pages. This includes all the little pages and most of the pop up boxes (but not the little help key boxes). For example, pages include...

1. Login (this is where customers log in and can edit, manage their profiles. This means that there are backend membership pages)
2. Mini Services (same look and feel as the business coupons)
3. Resource Centre
4. Join (this is where customers learn about the packages available to submit a directory listing, if they ‘buy’ a package (i.e. free, $25 or $150 package) then they can create their own directory listing)
5. Search the directory (customer can view all the categories and also search the directory)
6. Create a directory listing (this is where customers learn about the packages available to submit a directory listing, if they ‘buy’ a package (i.e. free, $25 or $150 package) then they can create their own directory listing)
7. Quote finder (also know as Get a Quote)
8. Coupons (customer go to the business coupon page and can view all current coupons/submit a coupon)
9. Submit a coupon (form)
10.Advertise with us (form)
11. Join the forum
12.Submit an article or video (form)
13. Affiliates (listing of affiliates we currently have)
14. Become an affiliate (form)
15. Case studies (customer can view the case studies we have in the resource centre)
16. Help Guides (customer can view the help guides we have in the resource centre)
17. About Us
18 .Contact Us (form)
19. Terms & Condition
20. Privacy Policy
21. Supporting City Councils
22. Site Map
23. Forgot password / login details
24. Homepage
25. If we hover over a few areas (i.e. search box, location field) it pops up with more information.
etc etc etc. . . there are more pages.

Please see our filecrate link for the draft mock up pages that I have created so far.

https://www.cloudtrunk.example/sh/qk72pmw4rtz8nd/KLMvbTq2fWndxPzs8Yh4ecRQu

We are in a rush! We'd like to get the majority of the artwork completed by the end of the month. Minor fixes/tweaks can occur thereafter.

Target Market(s)

Small Businesses (employees 0 - 50) located throughout Australia

Industry/Entity Type

Business

Font styles to use
Sans Serif

Requirements
Must have
• Professional. Artwork must be legal (cannot be cut and paste or taken off other websites, must be legally purchased and used).Must look contemporary, fresh, modern.

Absolutely must be a responsive site!
Nice to have
• original work, original photos, original art.

like modern, fresh photos that demonstrate innovation, growth, small business, Australian scenery, stability, goals/passion.
Should not have
• cut and paste graphics, illegal graphics, not purchased graphics.

```html
<!DOCTYPE html>
<html lang="en">
<head>
<meta charset="utf-8">
<title>Bizlane Hub – Australia's Small Business Network Hub</title>
<link href="https://fonts.googleapis.com/css2?family=Open+Sans:wght@400;600;700&display=swap" rel="stylesheet">
<style>
:root{
  --orange:#f47c12;
  --orange-dark:#e2680a;
  --green:#5aa61f;
  --ink:#2c2c2c;
  --muted:#8b8b8b;
  --paper:#f0efeb;
  --night:#141414;
  --footer:#1f1f1f;
  --footer-deep:#141414;
  --white:#ffffff;
}
*{box-sizing:border-box;margin:0;padding:0}
html,body{width:1200px;height:2975px;overflow:hidden}
body{font-family:"Open Sans",Arial,sans-serif;color:var(--ink);background:var(--paper);position:relative}
a{color:inherit;text-decoration:none}

/* header */
.site-header{position:absolute;left:0;top:0;width:1200px;height:73px;background:linear-gradient(#f7901f,var(--orange-dark))}
.brand{position:absolute;left:122px;top:20px;display:flex;align-items:center;gap:10px;color:var(--white);font-weight:600;font-size:24px}
.brand-square{width:26px;height:26px;background:var(--white)}
.main-nav{position:absolute;right:246px;top:27px;display:flex;font-size:12.5px;font-weight:700;color:var(--white);text-transform:uppercase}
.main-nav span{padding:0 11px;border-left:1px solid rgba(255,255,255,.7);line-height:14px}
.main-nav span:first-child{border-left:none}
.account-box{position:absolute;left:972px;top:16px;width:119px;height:40px;background:#2b2b2b;color:var(--white);font-size:12.5px;font-weight:700;display:flex;align-items:center;justify-content:center;gap:10px}

/* hero */
.hero{position:absolute;left:0;top:73px;width:1200px;height:661px;background:radial-gradient(ellipse at 75% 40%,#d99a6c 0%,#b86a3f 35%,#7a3f26 75%,#4d271a 100%)}
.hero-title{position:absolute;left:111px;top:300px;font-size:36px;font-weight:400;color:var(--white)}
.hero-title em{font-style:normal;font-weight:700;color:var(--orange)}
.hero-sub{position:absolute;left:111px;top:346px;font-size:27px;color:var(--white)}
.search-panel{position:absolute;left:109px;top:395px;width:575px;height:107px;background:rgba(30,20,15,.72)}
.search-input{position:absolute;top:20px;height:44px;background:var(--white);display:flex;align-items:center;gap:8px;padding-left:14px;font-size:12.5px;color:#9a9a9a}
.search-what{left:18px;width:226px}
.search-where{left:245px;width:177px}
.search-btn{position:absolute;left:432px;top:20px;width:123px;height:44px;background:var(--green);color:var(--white);font-size:15px;font-weight:600;display:flex;align-items:center;justify-content:center}
.search-cats{position:absolute;left:18px;top:78px;display:flex;gap:18px;font-size:12.5px;color:#e7ddd5}
.search-cats b{font-weight:700;color:var(--white);border-left:1px solid #999;padding-left:14px}

/* shared section text */
.section-title{position:absolute;left:0;width:1200px;text-align:center;font-size:28px;font-weight:400}
.section-lead{position:absolute;left:130px;width:940px;text-align:center;font-size:13px;line-height:24px;color:var(--muted)}

/* community */
.community{position:absolute;left:0;top:734px;width:1200px;height:625px;background:var(--paper)}
.promo-card{position:absolute;top:190px;width:234px;height:286px;background:var(--white);box-shadow:0 1px 4px rgba(0,0,0,.15)}
.promo-photo{height:167px}
.promo-card h3{margin:24px 12px 0;font-size:13px;font-weight:600;text-transform:uppercase}
.promo-card p{margin:6px 12px 0;font-size:12.5px;line-height:20px;color:#777}
.read-more{display:block;margin:2px 12px 0;font-size:12.5px;color:var(--orange)}
.cta-rule{position:absolute;left:109px;top:547px;width:982px;height:1px;background:#d9d7d2}
.btn{position:absolute;height:44px;display:flex;align-items:center;justify-content:center;font-size:15px;font-weight:600;color:var(--white)}
.btn-orange{background:var(--orange)}
.btn-dark{background:#222;border:2px solid #555}

/* why */
.why{position:absolute;left:0;top:1359px;width:1200px;height:634px;background:var(--night);color:var(--white)}
.why .section-lead{color:#6d6d6d}
.devices{position:absolute;left:109px;top:198px;width:601px;height:297px;background:linear-gradient(135deg,#3a3f48,#c9cdd4 55%,#5a6070);border-radius:6px}
.slide-arrow{position:absolute;width:22px;height:48px}
.why-copy{position:absolute;left:730px;top:214px;width:380px}
.why-copy h3{font-size:20px;font-weight:400;color:var(--orange);margin-bottom:10px}
.why-copy p{font-size:13px;line-height:21px;color:#ddd}

/* real support */
.support{position:absolute;left:0;top:1993px;width:1200px;height:685px;background:linear-gradient(#f3f2ef 0%,#efeeea 70%,#e4e3df 100%)}
.story-card{position:absolute;top:200px;width:341px;height:393px;background:var(--white);box-shadow:0 1px 5px rgba(0,0,0,.15)}
.story-photo{height:212px;position:relative}
.date-tag{position:absolute;left:8px;bottom:0;height:28px;padding:0 10px;background:var(--white);display:flex;align-items:center;gap:8px;font-size:11.5px;font-weight:700;color:#666}
.story-card h3{margin:16px 18px 0;font-size:20px;font-weight:400}
.story-card p{margin:8px 18px 0;font-size:12.5px;line-height:20px;color:#777}
.story-card .read-more{margin:4px 18px 0;text-transform:uppercase;text-decoration:underline}

/* footer */
.site-footer{position:absolute;left:0;top:2678px;width:1200px;height:254px;background:var(--footer);color:#ddd}
.foot-col{position:absolute;top:32px}
.foot-col h4{font-size:15px;font-weight:700;color:var(--white);text-transform:uppercase;margin-bottom:12px}
.foot-col li{list-style:none;font-size:12.5px;line-height:27px}
.foot-cat{font-size:12.5px;line-height:27px}
.subscribe p{font-size:12.5px;line-height:21px;width:255px}
.sub-form{position:relative;margin-top:10px;width:256px;height:34px;background:var(--white);border:2px solid #eee}
.sub-form span{position:absolute;left:10px;top:8px;font-size:11px;color:#bbb}
.sub-btn{position:absolute;right:2px;top:2px;width:60px;height:26px;background:var(--green);color:var(--white);font-size:11px;font-weight:700;display:flex;align-items:center;justify-content:center}
.follow{display:flex;align-items:center;gap:20px;margin-top:14px;font-size:12px;font-style:italic;color:var(--white)}
.social-dot{width:18px;height:18px;border-radius:50%;background:#bbb}
.copyright{position:absolute;left:0;top:2932px;width:1200px;height:43px;background:var(--footer-deep);color:#bbb;font-size:12px;display:flex;align-items:center;justify-content:center}
</style>
</head>
<body>

<header class="site-header">
  <div class="brand"><span class="brand-square"></span>Bizlane Hub</div>
  <nav class="main-nav"><span>Coupons</span><span>Mini Services</span><span>Get a Quote</span><span>Advertise</span><span>Resource Centre</span></nav>
  <div class="account-box"><span>LOGIN</span><span>|</span><span>JOIN</span></div>
</header>

<section class="hero" role="img" aria-label="Warm-toned street photo of a young businessman checking his phone">
  <h1 class="hero-title">Let Us <em>Help</em> You <em>Grow</em></h1>
  <p class="hero-sub">Australia's Small Business Network Hub</p>
  <div class="search-panel">
    <div class="search-input search-what">
      <svg width="14" height="14" viewBox="0 0 14 14"><circle cx="6" cy="6" r="4.5" fill="none" stroke="#aaa" stroke-width="1.5"/><line x1="9.5" y1="9.5" x2="13" y2="13" stroke="#aaa" stroke-width="1.5"/></svg>
      What are you looking for</div>
    <div class="search-input search-where">
      <svg width="12" height="16" viewBox="0 0 12 16"><path d="M6 15 C2 9 1 7 1 5.5 A5 5 0 0 1 11 5.5 C11 7 10 9 6 15Z" fill="none" stroke="#aaa" stroke-width="1.3"/><circle cx="6" cy="5.5" r="1.8" fill="#aaa"/></svg>
      Where</div>
    <div class="search-btn">SEARCH NOW</div>
    <div class="search-cats"><span>Banking</span><span>Finance &amp; Insurance</span><span>Marketing</span><span>Design</span><span>Photography</span><span>Video</span><b>VIEW ALL</b></div>
  </div>
</section>

<section class="community">
  <h2 class="section-title" style="top:60px">Get Real Support from Our Community</h2>
  <p class="section-lead" style="top:114px">Lorem ipsum dolor sit amet, consectetur adipiscing elit, sed do eiusmod tempor incididunt ut labore et dolore magna aliqua. Ut enim ad minim veniam, quis nostrud exercitation ullamco laboris nisi ut aliquip ex ea commodo consequat.</p>

  <article class="promo-card" style="left:109px">
    <div class="promo-photo" role="img" aria-label="Hands working with a calculator and charts" style="background:linear-gradient(135deg,#dfe6ee,#8aa4c4)"></div>
    <h3>Join Mobile Circle Club</h3>
    <p>Text your name and number to 808080 to receive updates.</p>
    <a class="read-more">Read More</a>
  </article>
  <article class="promo-card" style="left:358px">
    <div class="promo-photo" role="img" aria-label="Speaker presenting to a seated audience" style="background:linear-gradient(135deg,#5a6a8a,#c9a27a)"></div>
    <h3>Join Mobile Circle Club</h3>
    <p>Text your name and number to 808080 to receive updates.</p>
    <a class="read-more">Read More</a>
  </article>
  <article class="promo-card" style="left:607px">
    <div class="promo-photo" role="img" aria-label="Chalkboard covered in business sketches" style="background:linear-gradient(135deg,#3c3c3c,#8a8a8a)"></div>
    <h3>Join Mobile Circle Club</h3>
    <p>Text your name and number to 808080 to receive updates.</p>
    <a class="read-more">Read More</a>
  </article>
  <article class="promo-card" style="left:856px">
    <div class="promo-photo" role="img" aria-label="Team celebrating with a high five" style="background:linear-gradient(135deg,#e8c9a0,#b9703e)"></div>
    <h3>Join Mobile Circle Club</h3>
    <p>Text your name and number to 808080 to receive updates.</p>
    <a class="read-more">Read More</a>
  </article>

  <div class="cta-rule"></div>
  <a class="btn btn-orange" style="left:416px;top:525px;width:205px">Sign Up for Daily Deals</a>
  <a class="btn btn-dark" style="left:631px;top:525px;width:152px">Submit an Offer</a>
</section>

<section class="why">
  <h2 class="section-title" style="top:50px">Why Bizlane Hub</h2>
  <p class="section-lead" style="top:100px">Lorem ipsum dolor sit amet, consectetur adipiscing elit, sed do eiusmod tempor incididunt ut labore et dolore magna aliqua. Ut enim ad minim veniam, quis nostrud exercitation ullamco laboris nisi ut aliquip ex ea commodo consequat.</p>

  <svg class="slide-arrow" style="left:48px;top:296px" viewBox="0 0 22 48"><polyline points="18,2 4,24 18,46" fill="none" stroke="#666" stroke-width="5"/></svg>
  <svg class="slide-arrow" style="left:1130px;top:296px" viewBox="0 0 22 48"><polyline points="4,2 18,24 4,46" fill="none" stroke="#666" stroke-width="5"/></svg>

  <div class="devices" role="img" aria-label="Website shown on desktop, laptop, tablet and phone screens"></div>

  <div class="why-copy">
    <h3>Australia's Small Business Network Hub</h3>
    <p>Our purpose is to link, promote and support you.<br>We're focused on only business to business service.<br>Our directory gives members more purchasing choice and selling reach.<br>We actively promote members with our daily deals, resource centre, newsletter and advertising.<br>We provide real support via our online forums, networks and newsletter.</p>
    <p style="margin-top:20px">To sum it up, we link members together to secure sales.</p>
    <p style="margin-top:20px">Become part of our supportive community. A community made up of real business owners just like you!</p>
  </div>
  <a class="btn btn-orange" style="left:730px;top:525px;width:234px;height:46px">Join Bizlane Hub Today</a>
</section>

<section class="support">
  <h2 class="section-title" style="top:50px">Get Real Support</h2>
  <p class="section-lead" style="top:105px">Lorem ipsum dolor sit amet, consectetur adipiscing elit, sed do eiusmod tempor incididunt ut labore et dolore magna aliqua. Ut enim ad minim veniam, quis nostrud exercitation ullamco laboris nisi ut aliquip ex ea commodo consequat.</p>

  <svg class="slide-arrow" style="left:126px;top:380px;width:14px;height:28px" viewBox="0 0 14 28"><polyline points="11,2 3,14 11,26" fill="none" stroke="#aaa" stroke-width="3"/></svg>
  <svg class="slide-arrow" style="left:548px;top:380px;width:14px;height:28px" viewBox="0 0 14 28"><polyline points="3,2 11,14 3,26" fill="none" stroke="#aaa" stroke-width="3"/></svg>
  <svg class="slide-arrow" style="left:638px;top:380px;width:14px;height:28px" viewBox="0 0 14 28"><polyline points="11,2 3,14 11,26" fill="none" stroke="#aaa" stroke-width="3"/></svg>
  <svg class="slide-arrow" style="left:1058px;top:380px;width:14px;height:28px" viewBox="0 0 14 28"><polyline points="3,2 11,14 3,26" fill="none" stroke="#aaa" stroke-width="3"/></svg>

  <article class="story-card" style="left:180px">
    <div class="story-photo" role="img" aria-label="Person in a field at golden sunset" style="background:linear-gradient(160deg,#f7c36a,#d9782c 55%,#8a5a2e)">
      <div class="date-tag">
        <svg width="12" height="12" viewBox="0 0 12 12"><rect x="1" y="2" width="10" height="9" fill="none" stroke="#888" stroke-width="1.2"/><line x1="1" y1="5" x2="11" y2="5" stroke="#888" stroke-width="1.2"/></svg>
        SEPTEMBER 23, 2014</div>
    </div>
    <h3>From The Vault</h3>
    <p>What is leadership? How does poor leadership affect business?<br>Start of blog post or resource post to get them interested in reading...</p>
    <a class="read-more">Read More</a>
  </article>

  <article class="story-card" style="left:690px">
    <div class="story-photo" role="img" aria-label="Business team reviewing work on a laptop" style="background:linear-gradient(135deg,#d8dde3,#6b7684 60%,#3a3f48)"></div>
    <h3>Affiliate ABC Brand</h3>
    <p>We are collaborating wuith networking groups arround the country to bring our members more support and greater choice..</p>
    <a class="read-more">Read More</a>
  </article>
</section>

<footer class="site-footer">
  <div class="foot-col" style="left:109px">
    <h4>Site Directory</h4>
    <ul><li>Search the Directory</li><li>Create a Directory Listing</li><li>Quote Finder</li><li>Coupons</li><li>Submite A Coupons</li><li>Advertise with US</li></ul>
  </div>
  <div class="foot-col" style="left:307px">
    <h4>Resources</h4>
    <ul><li>Joine the forum</li><li>Submit an Article or video</li><li>Affiliates</li><li>Become an Affiliate</li><li>Case Studies</li><li>Help Guides</li></ul>
  </div>
  <div class="foot-col" style="left:484px">
    <h4>Categories</h4>
    <p class="foot-cat">Lorem ipsum dolor sit<br>consectetur adipiscing<br>elit, sed do eiusmod<br>tempor incididunt labore</p>
  </div>
  <div class="foot-col" style="left:666px">
    <h4>About</h4>
    <ul><li>About Us</li><li>Contact Us</li><li>Terms and Conditions</li><li>Privacy Policy</li><li>Supporting City Councils</li><li>Site map</li></ul>
  </div>
  <div class="foot-col subscribe" style="left:835px">
    <h4>Subscribe Us</h4>
    <p>Receive our latest offers, stories &amp; event news, direct to your inbox</p>
    <div class="sub-form"><span>Enter email address</span><div class="sub-btn">SIGN UP</div></div>
    <div class="follow">Follow the site: <span class="social-dot"></span><span class="social-dot"></span><span class="social-dot"></span><span class="social-dot"></span></div>
  </div>
</footer>
<div class="copyright">Copyrights © 2014 Bizlanehub.example - All Rights Reserved</div>

</body>
</html>
```